RM Tomás Ledesma (Business Card)

Hi designers, in this work, I'm looking for an sophisticated stylish, elegant and proffesional personal card. We have a laboratory of pathology automated, with equipments high quality.
In this web the designers, have created my business logo, the name is "RM Tomás Ledesma"
In our lab, we principal work is to prepare the biopsies for further diagnostic of diseases like cancer, tumors, etc.
I need that the first face, only having my complete logo (Rm Tomás Ledesma, Laboratorio de procesamiento Histologico)
The overleaf, could repeat the same logo, like water logo.
In this face, I need to say: My full data:

Técnico en Anatomía Patológica
Tomás Ledesma Urquiza M.P 48213
Av. Duarte Quirós 817 - 2do piso - Instituto Brandsen.
Córdoba, Argentina
(0351) 158246093
ledesma.tomas@correoviva.com.ar

with respect the colors of card, use your imagination, the original logo color is violet, I haven't chosen a color base for the card.

attached pictures are examples of cards I like your DESIGN.
Attached too, the original logo to my company.

the size of card are:
horizontal: 9cm
vertical: 5,5cm

any question that you have, not doubt to question me,
Hand to work!

Industry/Entity Type

Laboratory

Requirements
Must have
• designers sophisticated, not simples, like show the images attached

```html
<!DOCTYPE html>
<html lang="es">
<head>
<meta charset="utf-8">
<title>Tomás Ledesma – Tarjeta personal</title>
<link rel="stylesheet" href="https://fonts.googleapis.com/css2?family=Open+Sans:ital,wght@0,400;0,700;1,400&family=Roboto+Condensed:wght@400&display=swap">
<style>
  :root {
    --bg: #e9e7ec;
    --card-white: #fbfbfb;
    --violet: #7a2fc0;
    --violet-deep: #5d1f9e;
    --violet-light: #9b4fd6;
    --grey-text: #7b7b7f;
    --grey-soft: #a3a3a8;
    --white: #ffffff;
  }
  * { margin: 0; padding: 0; box-sizing: border-box; }
  html, body { width: 1200px; height: 658px; overflow: hidden; }
  body {
    background: var(--bg);
    font-family: "Open Sans", sans-serif;
    position: relative;
  }
  .card {
    position: absolute;
    top: 192px;
    width: 450px;
    height: 275px;
    border-radius: 16px;
    overflow: hidden;
    background: var(--card-white);
    box-shadow: 0 6px 18px rgba(40, 20, 60, 0.18);
  }
  .card--front { left: 90px; }
  .card--back { left: 660px; }

  /* Front */
  .front-brand {
    position: absolute;
    left: 0; right: 0; top: 92px;
    display: flex;
    align-items: center;
    justify-content: center;
    gap: 12px;
  }
  .brand-mark {
    width: 30px; height: 30px;
    border: 2px solid var(--violet);
    border-radius: 4px;
  }
  .brand-name {
    font-family: "Roboto Condensed", sans-serif;
    font-size: 30px;
    font-weight: 400;
    letter-spacing: 1px;
    color: var(--grey-text);
  }
  .front-rule {
    position: absolute;
    left: 78px; right: 78px; top: 146px;
    height: 1px;
    background: var(--grey-soft);
  }
  .front-tagline {
    position: absolute;
    left: 0; right: 0; top: 154px;
    text-align: center;
    font-family: "Roboto Condensed", sans-serif;
    font-size: 17px;
    letter-spacing: 0.3px;
    text-transform: uppercase;
    color: var(--grey-text);
  }

  /* Back */
  .back-band { position: absolute; inset: 0; }
  .back-brand {
    position: absolute;
    left: 22px; top: 112px;
    width: 200px;
    color: var(--white);
  }
  .back-brand .brand-row { display: flex; align-items: center; gap: 8px; }
  .back-brand .brand-mark { width: 18px; height: 18px; border-color: var(--white); border-radius: 3px; }
  .back-brand .brand-name { font-size: 18px; color: var(--white); }
  .back-brand .front-tagline-small {
    margin-top: 6px;
    padding-top: 5px;
    border-top: 1px solid rgba(255,255,255,0.7);
    font-family: "Roboto Condensed", sans-serif;
    font-size: 9.5px;
    text-transform: uppercase;
    letter-spacing: 0.2px;
  }
  .contact {
    position: absolute;
    left: 296px; top: 30px;
    width: 150px;
    font-size: 9px;
    line-height: 1.45;
    color: var(--grey-text);
  }
  .contact-name {
    font-size: 11px;
    font-weight: 700;
    color: var(--violet);
    line-height: 1.3;
  }
  .contact-role { font-style: italic; color: var(--grey-soft); margin-bottom: 26px; }
  .contact-address { margin-bottom: 20px; }
  .contact-phone { margin-bottom: 22px; }
  .contact-email { color: var(--violet); font-size: 8.4px; }
</style>
</head>
<body>

<section class="card card--front" aria-label="Frente de la tarjeta">
  <div class="front-brand">
    <span class="brand-mark"></span>
    <span class="brand-name">RM Tomás Ledesma</span>
  </div>
  <div class="front-rule"></div>
  <p class="front-tagline">Laboratorio de procesamiento histológico</p>
</section>

<section class="card card--back" aria-label="Dorso de la tarjeta">
  <svg class="back-band" width="450" height="275" viewBox="0 0 450 275" aria-hidden="true">
    <defs>
      <linearGradient id="bandGradient" x1="0" y1="0" x2="1" y2="1">
        <stop offset="0" stop-color="#9b4fd6"/>
        <stop offset="0.55" stop-color="#7a2fc0"/>
        <stop offset="1" stop-color="#5d1f9e"/>
      </linearGradient>
    </defs>
    <path d="M0 0 H262 L262 94 L270 100 L262 106 L262 134 L270 140 L262 146 L262 174 L270 180 L262 186 L262 275 H0 Z" fill="url(#bandGradient)"/>
    <!-- pin -->
    <circle cx="248" cy="100" r="11" fill="#ffffff"/>
    <path d="M248 94 a4 4 0 0 1 4 4 c0 3 -4 8 -4 8 s-4 -5 -4 -8 a4 4 0 0 1 4 -4 z" fill="#7a2fc0"/>
    <circle cx="248" cy="98" r="1.5" fill="#ffffff"/>
    <!-- phone -->
    <circle cx="248" cy="140" r="11" fill="#ffffff"/>
    <rect x="244" y="133" width="8" height="14" rx="1.5" fill="#7a2fc0"/>
    <rect x="245.5" y="135" width="5" height="8" fill="#ffffff"/>
    <!-- mail -->
    <circle cx="248" cy="180" r="11" fill="#ffffff"/>
    <rect x="242" y="176" width="12" height="9" fill="#7a2fc0"/>
    <path d="M242 176 L248 181 L254 176" stroke="#ffffff" stroke-width="1" fill="none"/>
  </svg>

  <div class="back-brand">
    <div class="brand-row">
      <span class="brand-mark"></span>
      <span class="brand-name">RM Tomás Ledesma</span>
    </div>
    <p class="front-tagline-small">Laboratorio de procesamiento histológico</p>
  </div>

  <div class="contact">
    <p class="contact-name">Tomás Ledesma Urquiza M.P 48213</p>
    <p class="contact-role">Técnico en Anatomía Patológica</p>
    <p class="contact-address">Av. Duarte Quirós 817 - 2do piso<br>Instituto Brandsen.<br>Córdoba, Argentina</p>
    <p class="contact-phone">(0351) 158246093</p>
    <p class="contact-email">ledesma.tomas@correoviva.com.ar</p>
  </div>
</section>

</body>
</html>
```